Global (re)insurance broker needs a business card design

We need a classic business card for our company that is headquartered in SG, with offices in Malaysia and Dubai. We specialise in insurance and reinsurance broking and consultancy for our global clients.

```html
<!DOCTYPE html>
<html lang="en">
<head>
<meta charset="utf-8">
<title>Norvane Business Card</title>
<link href="https://fonts.googleapis.com/css2?family=Open+Sans:wght@400;700&display=swap" rel="stylesheet">
<style>
  :root {
    --stage: #2b2b2e;
    --card: #151515;
    --blue: #274a9c;
    --mint: #c4ddb8;
    --text: #f2f2f2;
  }
  * { margin: 0; padding: 0; box-sizing: border-box; }
  html, body { width: 1200px; height: 947px; overflow: hidden; }
  body {
    background: var(--stage);
    font-family: "Open Sans", Arial, sans-serif;
    display: flex;
    flex-direction: column;
    align-items: center;
    justify-content: center;
    gap: 48px;
  }
  .card {
    position: relative;
    width: 620px;
    height: 360px;
    background: var(--card);
    border-radius: 22px;
    overflow: hidden;
    box-shadow: 0 12px 30px rgba(0,0,0,.45);
  }
  .card-front { display: flex; align-items: center; justify-content: center; }
  .brand-name {
    font-weight: 700;
    color: var(--mint);
    letter-spacing: 4px;
    line-height: 1;
  }
  .card-front .brand-name { font-size: 76px; }

  .card-back .brand-name {
    position: absolute;
    left: 40px;
    top: 140px;
    font-size: 44px;
  }
  .divider {
    position: absolute;
    left: 318px;
    top: 40px;
    width: 1.5px;
    height: 230px;
    background: var(--mint);
  }
  .contact {
    position: absolute;
    left: 340px;
    top: 46px;
    color: var(--text);
  }
  .contact-name { font-weight: 700; font-size: 22px; color: var(--blue); }
  .contact-name .surname { color: var(--mint); }
  .contact-role { font-size: 15px; margin-bottom: 14px; }
  .contact-line {
    display: flex; align-items: center; gap: 8px;
    font-size: 14px; line-height: 1.55;
  }
  .contact-line svg { width: 12px; height: 12px; fill: var(--text); flex: none; }
  .contact-address { font-size: 14px; line-height: 1.5; margin-top: 14px; }
  .swoosh { position: absolute; left: 0; bottom: 0; width: 620px; height: 360px; }
</style>
</head>
<body>
  <section class="card card-front">
    <div class="brand-name">NORVANE</div>
  </section>

  <section class="card card-back">
    <svg class="swoosh" viewBox="0 0 620 360" aria-hidden="true">
      <path d="M60 360 C 190 300 360 270 620 262 L620 290 C 380 296 220 322 110 360 Z" fill="var(--blue)"/>
      <path d="M130 360 C 250 314 420 288 620 282 L620 292 C 420 300 260 326 150 360 Z" fill="var(--mint)"/>
      <path d="M170 360 C 290 328 440 306 620 300 L620 360 Z" fill="var(--blue)"/>
    </svg>
    <div class="brand-name">NORVANE</div>
    <div class="divider"></div>
    <div class="contact">
      <div class="contact-name">Mira <span class="surname">Lee</span></div>
      <div class="contact-role">Chief Operating Officer</div>
      <div class="contact-line">
        <svg viewBox="0 0 24 24"><path d="M6.6 10.8a15 15 0 0 0 6.6 6.6l2.2-2.2a1 1 0 0 1 1-.25 11.4 11.4 0 0 0 3.6.57 1 1 0 0 1 1 1V20a1 1 0 0 1-1 1A17 17 0 0 1 3 4a1 1 0 0 1 1-1h3.5a1 1 0 0 1 1 1c0 1.25.2 2.45.57 3.57a1 1 0 0 1-.25 1z"/></svg>
        <span>+65 9000 1234</span>
      </div>
      <div class="contact-line">
        <svg viewBox="0 0 24 24"><path d="M2 5h20v14H2z M2 5l10 8 10-8" /></svg>
        <span>mira@norvane.com</span>
      </div>
      <div class="contact-line">
        <svg viewBox="0 0 24 24"><circle cx="12" cy="12" r="10"/></svg>
        <span>www.norvane.com</span>
      </div>
      <div class="contact-address">
        22 Harbour Lane,<br>
        Meridian Tower #08-04,<br>
        Singapore 018900
      </div>
    </div>
  </section>
</body>
</html>
```